Blow Dry Bar Business Cards

These cards must be eye catching and modern.
You must be willing to work fast and make changes.

Winner will be offered other projects

Files 1 THIS IS THE STYLE CARDS I AM INTRESTED IN!!!
Please be creative, I am paying for my own eye catching design. I need files to be nexa press ready.

COLORS THAT ARE PAINTED INSIDE MY SHOP:
- - - http://www.quorvelpaint.example/en/explore-colors/painter/color-selector.html?colors=4007-3C

- - - http://www.brandivex.example/color/paint-colors/hidden-corridor-d58-2

I want the business cards sleek and modern if you use the logo please correct imperfections. I added the part that says Blow Dry Bar (see website).
Do not be afraid to separate the blow dryer from the name to make the cards look like the file with the pink elephant.

SHOULD INCLUDE
*Blow Dryer (we are a blow dry bar not a salon we do not cut or color so do not include sheers of any kind)
*BUSINESS NAME: Simply Swept Upward - Blow Dry Bar (PLEASE SEE MY WEBSITE)
* Website: SIMPLYSWEPTUPWARD.EXAMPLE
*Phone number (555) 014-2763
Updates

Nexa press said it can be submitted in JPG

http://www.brandivex.example/color/paint-colors/hidden-corridor-d58-2 http://www.quorvelpaint.example/en/explore-colors/painter/color-selector.html?colors=4007-3C ^^^^ These links will take you to the color paint that is painted inside my shop.

Target Market(s)

AGES 18 - 55 WOMEN
HIGH END MARKET

Industry/Entity Type

Salon

Requirements
Must have
• SEE COLOR EXAMPLE FILE
BLOW DRYER
UNIQUE
I LIKE THE CARD WITH THE PINK ELEPHANT THE BEST
Nice to have
• BE AS CREATIVE AND MODERN AS POSSIBLE DO NOT COPY ANY OF THE CARDS BELOW.
Should not have
• SCISSORS
PINK

```html
<!DOCTYPE html>
<html lang="en">
<head>
<meta charset="utf-8">
<title>Blow Dry Bar Business Cards</title>
<link href="https://fonts.googleapis.com/css2?family=Josefin+Sans:wght@300;400&family=Quicksand:wght@300;500&display=swap" rel="stylesheet">
<style>
  :root {
    --backdrop: #e9e6e2;
    --card: #fbfbfa;
    --card-edge: #d9d7d4;
    --ink: #4a3530;
    --ink-soft: #6a5650;
    --band: #4b3833;
    --band-text: #f4efec;
  }
  html, body {
    margin: 0;
    padding: 0;
    width: 1200px;
    height: 885px;
    overflow: hidden;
    background: var(--backdrop);
  }
  .canvas {
    width: 1200px;
    height: 885px;
    display: flex;
    align-items: center;
    justify-content: center;
    gap: 44px;
  }
  .card {
    position: relative;
    width: 540px;
    height: 309px;
    background: var(--card);
    border-radius: 16px;
    box-shadow: 0 2px 0 var(--card-edge), 0 10px 24px rgba(60, 40, 30, 0.18);
    overflow: hidden;
    color: var(--ink);
  }

  /* Front: details */
  .front .title {
    position: absolute;
    left: 0;
    right: 0;
    top: 50px;
    margin: 0;
    text-align: center;
    font-family: "Quicksand", sans-serif;
    font-weight: 300;
    font-size: 50px;
    letter-spacing: 1px;
    color: var(--ink);
  }
  .front .rule-row {
    position: absolute;
    left: 0;
    right: 0;
    top: 128px;
    display: flex;
    align-items: center;
    gap: 14px;
  }
  .front .rule-row .line {
    height: 1px;
    background: var(--ink);
  }
  .front .rule-row .line.lead { width: 200px; }
  .front .rule-row .line.tail { flex: 1; }
  .front .owners {
    font-family: "Quicksand", sans-serif;
    font-weight: 500;
    font-size: 17px;
    color: var(--ink);
  }
  .front .contact {
    position: absolute;
    left: 214px;
    right: 20px;
    top: 162px;
    margin: 0;
    padding: 0;
    list-style: none;
    font-family: "Josefin Sans", sans-serif;
    font-weight: 300;
    font-size: 14px;
    line-height: 29px;
    letter-spacing: 0.4px;
    white-space: nowrap;
    color: var(--ink-soft);
  }
  .front .address-band {
    position: absolute;
    left: 0;
    right: 0;
    bottom: 0;
    height: 34px;
    background: var(--band);
    display: flex;
    align-items: center;
    justify-content: center;
    font-family: "Josefin Sans", sans-serif;
    font-weight: 400;
    font-size: 14.5px;
    letter-spacing: 0.6px;
    text-transform: uppercase;
    color: var(--band-text);
  }

  /* Back: name */
  .back .brand {
    position: absolute;
    left: 0;
    right: 0;
    top: 88px;
    display: flex;
    align-items: center;
    justify-content: center;
    gap: 16px;
  }
  .back .brand-name {
    font-family: "Quicksand", sans-serif;
    font-weight: 500;
    font-size: 40px;
    color: var(--ink);
  }
  .back .brand-dot {
    width: 26px;
    height: 26px;
    border-radius: 50%;
    background: var(--ink);
  }
  .back .website {
    position: absolute;
    left: 120px;
    top: 178px;
    font-family: "Josefin Sans", sans-serif;
    font-weight: 300;
    font-size: 14px;
    letter-spacing: 0.8px;
    color: var(--ink-soft);
  }
  .back .short-rule {
    position: absolute;
    left: 120px;
    top: 220px;
    width: 70px;
    height: 1px;
    background: var(--ink);
  }
</style>
</head>
<body>
  <main class="canvas">
    <section class="card front" aria-label="Card front with contact details">
      <h1 class="title">Blow Dry Bar</h1>
      <div class="rule-row">
        <span class="line lead"></span>
        <span class="owners">Marisol&amp;Kate</span>
        <span class="line tail"></span>
      </div>
      <ul class="contact">
        <li>(555) 014-2763</li>
        <li>SIMPLYSWEPTUPWARD.EXAMPLE</li>
        <li>INFO@SIMPLYSWEPTUPWARD.EXAMPLE</li>
      </ul>
      <div class="address-band">412 Willow Bend Road Suite 9 Fairhaven, Texas 75010</div>
    </section>

    <section class="card back" aria-label="Card back with business name">
      <div class="brand">
        <span class="brand-name">Simply Swept Upward</span>
        <span class="brand-dot"></span>
      </div>
      <div class="website">SIMPLYSWEPTUPWARD.EXAMPLE</div>
      <div class="short-rule"></div>
    </section>
  </main>
</body>
</html>
```